Modern Attractive Letterhead for Veterinary House Call Business.

A letterhead which can be printed on A4, A5 and A6 paper sizes.
To have: ( our files to be uploaded)
1. Logo with Text
2. telephone
3. email
4. website
5. Address

Target Market(s)

60-85year mainly women pet owners. Also market include families, young professionals, busy people who have dogs and cats

Industry/Entity Type

Business

Requirements
Must have
• 1. Logo with Text ( provided)
• 2. telephone
• 3. email
• 4. website
• 5. Address
Nice to have
• Needs to be modern, preferably warm and caring in nature( if possible )
Should not have
• difficulty in printing A5 and A6

```html
<!DOCTYPE html>
<html lang="en">
<head>
<meta charset="utf-8">
<title>Kindred Vet Visits – Letterhead</title>
<link rel="stylesheet" href="https://fonts.googleapis.com/css2?family=Cinzel:wght@400;600&display=swap">
<style>
  :root {
    --backdrop: #ebe8e3;
    --paper: #ffffff;
    --navy: #1f2a6b;
    --sky: #3a9fe0;
    --brand-blue: #1f5fa8;
    --ink: #2b2b2b;
    --icon-green: #3c9a3a;
  }
  * { margin: 0; padding: 0; box-sizing: border-box; }
  html, body {
    width: 901px;
    height: 1200px;
    overflow: hidden;
    background: var(--backdrop);
  }
  .canvas {
    position: relative;
    width: 901px;
    height: 1200px;
  }
  .letterhead {
    position: absolute;
    left: 44px;
    top: 39px;
    width: 796px;
    height: 1126px;
    background: var(--paper);
    box-shadow: 0 1px 4px rgba(0,0,0,0.12);
    font-family: "Cinzel", serif;
    color: var(--ink);
  }
  .brand {
    position: absolute;
    left: 0;
    right: 0;
    top: 72px;
    display: flex;
    justify-content: center;
    align-items: center;
    gap: 14px;
  }
  .brand-dot {
    width: 46px;
    height: 46px;
    border-radius: 50%;
    background: var(--brand-blue);
  }
  .brand-name {
    font-family: "Cinzel", serif;
    font-weight: 600;
    font-size: 38px;
    letter-spacing: 0.5px;
    color: var(--brand-blue);
  }
  .header-rule {
    position: absolute;
    left: 0;
    top: 150px;
    width: 501px;
    height: 3px;
    background: linear-gradient(90deg, var(--navy), var(--sky));
  }
  .header-web {
    position: absolute;
    left: 518px;
    top: 143px;
    font-size: 12.5px;
    letter-spacing: 0.3px;
    color: var(--ink);
  }
  .header-rule-end {
    position: absolute;
    left: 729px;
    top: 150px;
    width: 67px;
    height: 3px;
    background: var(--navy);
  }
  .footer {
    position: absolute;
    left: 0;
    right: 0;
    top: 1094px;
    display: flex;
    justify-content: center;
    align-items: center;
    gap: 8px;
    font-size: 13px;
    white-space: nowrap;
  }
  .footer-item {
    display: flex;
    align-items: center;
    gap: 5px;
  }
  .footer-item svg { display: block; }
  .footer-divider { color: #888; margin: 0 4px; }
  .footer-address { font-size: 15px; }
</style>
</head>
<body>
<div class="canvas">
  <div class="letterhead">
    <div class="brand">
      <span class="brand-dot"></span>
      <span class="brand-name">Kindred Vet Visits</span>
    </div>

    <div class="header-rule"></div>
    <div class="header-web">www.kindredvetvisits.com.au</div>
    <div class="header-rule-end"></div>

    <div class="footer">
      <span class="footer-item">
        <svg width="11" height="11" viewBox="0 0 12 12" aria-hidden="true">
          <circle cx="6" cy="6" r="5.3" fill="none" stroke="var(--icon-green)" stroke-width="1.2"/>
          <path d="M4 3.2 L5 4.8 L4.5 5.4 Q5.3 7 6.7 7.6 L7.3 7 L8.8 8 L8 9 Q5.5 8.6 3.3 4.2 Z" fill="var(--icon-green)"/>
        </svg>
        0400555012
      </span>
      <span class="footer-item">
        <svg width="13" height="10" viewBox="0 0 13 10" aria-hidden="true">
          <rect x="0.5" y="2" width="12" height="7.5" rx="1" fill="var(--icon-green)"/>
          <path d="M0.5 2.5 L6.5 6.5 L12.5 2.5" fill="none" stroke="#fff" stroke-width="1"/>
        </svg>
        info@kindredvetvisits.com.au
      </span>
      <span class="footer-divider">|</span>
      <span class="footer-address">PO Box 2140 Riverbend QLD 4000</span>
    </div>
  </div>
</div>
</body>
</html>
```